Professional Personal Website with Blog and four sections

I am seeking a website design for myself. I would like the site to contain a blog, related to Information Security and several sections.

I am an established Information Security Consultant (one aspect of the site).
I am an author of a children's spiritual book that is "new thought" (another aspect of the site)
I am a co-founder of a secure social platform for kids and families (www.bramlowt.com)
I may want a section on finance as well, not sure at this moment

I want this site to be a personal website, not a subscription service or professional services sales site, I want the site to look very professional, so that I can share it with all types of people without concern - business, spiritual, other.

I have provided a photo of myself for the site, smart casual on a beach. The site will be hosted on dorianhelpe.com

You can see samples of what I am referring to by searching "personal website" on images.zentrova.com

I would like the page layout, and the images chopped up as individual jpgs, including hover images for buttons. I can do the coding

I would like the following buttons
Home, About, Information Security Blog, Passion Projects, Contact

I would like the top portion of the page to say "Tobin Marsh"
I would like the subtext to say:
Executive Information Security Architect, Author, and Idea Man

I envision the following

Target Market(s)

Executive / Technical / Creative types / Spritual types

Number of Pages Required

4 page

Requirements
Must have
• Blog section
Should not have
• No Matrix themes or No Cop themes, No Fingerprints or Eyeball scans

```html
<!DOCTYPE html>
<html lang="en">
<head>
<meta charset="utf-8">
<title>Tobin Marsh</title>
<link href="https://fonts.googleapis.com/css2?family=Roboto+Condensed:wght@400;700&family=Open+Sans:wght@400;600&display=swap" rel="stylesheet">
<style>
:root{
  --ink:#222;
  --muted:#888;
  --body:#666;
  --page:#e6e6e6;
  --card:#fff;
  --dark:#161616;
  --dark-2:#222;
  --line:#3a3a3a;
  --accent:#f26522;
  --accent-dark:#d9531a;
  --rule:#ececec;
}
*{box-sizing:border-box;margin:0;padding:0}
html,body{width:1200px;height:2928px;overflow:hidden}
body{background:var(--page);font-family:"Open Sans",sans-serif;color:var(--body);position:relative}
.display{font-family:"Roboto Condensed",sans-serif}

/* header */
.site-header{position:absolute;top:0;left:0;width:1200px;height:180px;background:linear-gradient(#1f1f1f,#121212)}
.site-title{position:absolute;top:38px;width:100%;text-align:center;font-family:"Roboto Condensed",sans-serif;font-weight:700;font-size:40px;letter-spacing:2px;color:#fff}
.main-nav{position:absolute;top:104px;left:132px;width:936px;height:46px;border-top:1px solid var(--line);border-bottom:1px solid var(--line);display:flex;align-items:center;padding:0 18px;gap:38px}
.main-nav a{font-family:"Roboto Condensed",sans-serif;font-weight:700;font-size:14px;color:#ddd;text-decoration:none;letter-spacing:.5px}
.main-nav .search-icon{margin-left:auto}

/* hero */
.hero{position:absolute;top:192px;left:132px;width:936px;height:480px;border:6px solid #fff;overflow:hidden}
.hero-media{position:absolute;inset:0;background:radial-gradient(circle at 70% 40%,#3b6b3a 0%,#173a2c 35%,#0b1f2a 70%,#071018 100%)}
.hero-copy{position:absolute;top:90px;left:28px;width:420px;color:#fff}
.hero-copy h1{font-family:"Roboto Condensed",sans-serif;font-weight:700;font-size:34px;letter-spacing:.5px;margin-bottom:14px}
.hero-copy p{font-size:12px;line-height:20px;color:#e4e4e4;margin-bottom:10px}
.hero-copy .lead{font-weight:600;text-transform:uppercase;color:#fff}
.btn{display:inline-block;background:var(--accent);color:#fff;font-family:"Roboto Condensed",sans-serif;font-weight:700;font-size:13px;border-radius:18px;padding:9px 22px;letter-spacing:.5px}
.hero-copy .btn{margin-top:14px}
.slider-arrows{position:absolute;right:14px;bottom:14px;display:flex;gap:4px}
.slider-arrows span{width:26px;height:26px;background:#ddd;display:flex;align-items:center;justify-content:center}

/* posts */
.post{position:absolute;left:132px;width:616px;height:460px;background:var(--card);padding:18px 20px}
.post-head{display:flex;align-items:center;gap:14px;padding-bottom:12px;border-bottom:1px solid var(--rule)}
.post-icon{width:36px;height:36px;border-radius:50%;border:2px solid var(--accent);display:flex;align-items:center;justify-content:center;flex:none}
.post-title{font-family:"Roboto Condensed",sans-serif;font-weight:700;font-size:17px;color:var(--ink);text-transform:uppercase}
.post-meta{display:flex;gap:22px;font-size:11px;color:var(--muted);padding:8px 0 10px 50px}
.post-meta span::before{content:"";display:inline-block;width:8px;height:8px;border-radius:50%;background:#bbb;margin-right:6px;vertical-align:middle}
.post-media{height:226px;width:100%}
.post-excerpt{font-size:11.5px;line-height:18px;margin:12px 0 14px}
.post-actions{display:flex;align-items:center;justify-content:space-between}
.share{display:flex;gap:5px}
.share i{width:24px;height:24px;border-radius:50%;display:block}

/* sidebar */
.widget{position:absolute;left:772px;width:296px;background:var(--card)}
.widget-title{font-family:"Roboto Condensed",sans-serif;font-weight:700;font-size:14px;color:var(--ink);text-align:center;padding:14px 0 12px;border-bottom:1px solid var(--rule);margin:0 16px 14px}
.search{top:712px;height:56px;display:flex;align-items:center;padding:0 12px}
.search-box{flex:1;height:34px;border:1px solid #ddd;font-size:12px;color:#aaa;padding:9px 10px}
.search-btn{width:34px;height:34px;background:var(--accent);display:flex;align-items:center;justify-content:center}
.about{top:784px;height:320px;padding-bottom:16px}
.about-media{margin:0 16px;height:150px;background:linear-gradient(135deg,#2a3d8f,#5a2f8a 55%,#1a1f5a)}
.about p{font-size:11.5px;line-height:18px;text-align:center;margin:12px 20px 0}
.connect{top:1120px;height:112px}
.connect .share{justify-content:center;gap:8px}
.connect .share i{width:26px;height:26px}
.recent{top:1248px;height:360px}
.recent-item{display:flex;gap:12px;align-items:center;margin:0 16px 16px}
.recent-thumb{width:84px;height:56px;flex:none}
.recent-item h4{font-family:"Roboto Condensed",sans-serif;font-size:12px;color:var(--ink);margin-bottom:6px}
.recent-item small{font-size:10px;color:var(--muted)}
.tweets{top:1624px;height:364px}
.tweet{display:flex;gap:10px;margin:0 16px 16px}
.tweet p{font-size:11.5px;line-height:17px;color:var(--ink)}
.tweet a{color:var(--accent);text-decoration:none}
.tweet small{display:block;font-size:10px;color:var(--muted);margin-top:2px}
.photos{top:2004px;height:200px}
.photo-grid{display:grid;grid-template-columns:repeat(4,1fr);gap:6px;margin:0 16px}
.photo-grid i{display:block;height:58px}

/* footer */
.site-footer{position:absolute;top:2784px;left:0;width:1200px;height:144px;background:var(--dark)}
.footer-nav{position:absolute;top:40px;width:100%;display:flex;justify-content:center;gap:38px}
.footer-nav a{font-family:"Roboto Condensed",sans-serif;font-weight:700;font-size:13px;color:#ccc;text-decoration:none}
.copyright{position:absolute;top:82px;width:100%;text-align:center;font-size:11px;color:#aaa;letter-spacing:.5px}
</style>
</head>
<body>

<header class="site-header">
  <div class="site-title">TOBINMARSH</div>
  <nav class="main-nav">
    <a href="#">HOME</a><a href="#">DEMO</a><a href="#">BLOG</a><a href="#">CATEGORIES</a><a href="#">POST FORMATS</a><a href="#">AUTHORS</a><a href="#">PORTFOLIO</a><a href="#">ELEMENTS</a>
    <svg class="search-icon" width="16" height="16" viewBox="0 0 16 16"><circle cx="6.5" cy="6.5" r="5" fill="none" stroke="#ddd" stroke-width="2"/><line x1="10.5" y1="10.5" x2="15" y2="15" stroke="#ddd" stroke-width="2"/></svg>
  </nav>
</header>

<section class="hero">
  <div class="hero-media" role="img" aria-label="Padlock resting on a glowing green circuit board"></div>
  <div class="hero-copy">
    <h1>WELCOME TO TOBINMARSH</h1>
    <p class="lead">Security thinking, stories for young minds and a safer social space for families, all gathered in one place.</p>
    <p>Here you will find notes from years of guiding firms through risk, plus the quieter projects I care about most.</p>
    <p>Read, share and come back often for new posts.</p>
    <span class="btn">READ MORE</span>
  </div>
  <div class="slider-arrows">
    <span><svg width="8" height="10" viewBox="0 0 8 10"><path d="M6 1 2 5l4 4" fill="none" stroke="#555" stroke-width="2"/></svg></span>
    <span><svg width="8" height="10" viewBox="0 0 8 10"><path d="M2 1l4 4-4 4" fill="none" stroke="#555" stroke-width="2"/></svg></span>
  </div>
</section>

<!-- posts -->
<article class="post" style="top:712px">
  <div class="post-head">
    <span class="post-icon"><svg width="16" height="16" viewBox="0 0 16 16"><path d="M2 14l1-4 8-8 3 3-8 8z" fill="var(--accent)"/></svg></span>
    <h2 class="post-title">I am an established Information Security Consultant</h2>
  </div>
  <div class="post-meta"><span>Tobin Marsh</span><span>17 Oct 2015</span><span>9835 Views</span><span>Comments</span></div>
  <div class="post-media" role="img" aria-label="Golden key on a dark circuit board with glowing traces" style="background:radial-gradient(circle at 40% 50%,#c9772a,#5a2a12 50%,#1c0e08)"></div>
  <p class="post-excerpt">Two decades spent mapping threats, building defences and helping leaders weigh risk have taught me that good security starts with clear thinking and honest conversations. Here I share what works and what does not.</p>
  <div class="post-actions"><span class="btn">READ MORE</span>
    <div class="share"><i style="background:#3b5998"></i><i style="background:#1da1f2"></i><i style="background:#dd4b39"></i><i style="background:#cb2027"></i><i style="background:#0077b5"></i><i style="background:#e4405f"></i><i style="background:#00aced"></i></div>
  </div>
</article>

<article class="post" style="top:1192px">
  <div class="post-head">
    <span class="post-icon"><svg width="16" height="16" viewBox="0 0 16 16"><path d="M2 14l1-4 8-8 3 3-8 8z" fill="var(--accent)"/></svg></span>
    <h2 class="post-title">I am an author of a children's spiritual book that is "new thought"</h2>
  </div>
  <div class="post-meta"><span>Tobin Marsh</span><span>17 Oct 2015</span><span>9835 Views</span><span>Comments</span></div>
  <div class="post-media" role="img" aria-label="Glowing processor chip with orange light lines on black" style="background:radial-gradient(circle at 50% 50%,#f0a040,#8a3a10 35%,#1a0a04 75%)"></div>
  <p class="post-excerpt">My book invites children to notice their thoughts, trust their inner voice and treat others with kindness. It grew from bedtime talks and gentle questions, and I hope it opens the same calm space for your family.</p>
  <div class="post-actions"><span class="btn">READ MORE</span>
    <div class="share"><i style="background:#3b5998"></i><i style="background:#1da1f2"></i><i style="background:#dd4b39"></i><i style="background:#cb2027"></i><i style="background:#0077b5"></i><i style="background:#e4405f"></i><i style="background:#00aced"></i></div>
  </div>
</article>

<article class="post" style="top:1672px">
  <div class="post-head">
    <span class="post-icon"><svg width="16" height="16" viewBox="0 0 16 16"><path d="M2 14l1-4 8-8 3 3-8 8z" fill="var(--accent)"/></svg></span>
    <h2 class="post-title">I am a co-founder of a secure social platform for kids and families</h2>
  </div>
  <div class="post-meta"><span>Tobin Marsh</span><span>17 Oct 2015</span><span>9835 Views</span><span>Comments</span></div>
  <div class="post-media" role="img" aria-label="Red padlock over a blue digital grid" style="background:radial-gradient(circle at 45% 55%,#b0202a,#2a3a7a 45%,#0c1a40)"></div>
  <p class="post-excerpt">At www.bramlowt.com we built a place where kids can share, learn and play while parents stay close. Privacy comes first, every feature is designed with families in mind, and nothing is sold to advertisers.</p>
  <div class="post-actions"><span class="btn">READ MORE</span>
    <div class="share"><i style="background:#3b5998"></i><i style="background:#1da1f2"></i><i style="background:#dd4b39"></i><i style="background:#cb2027"></i><i style="background:#0077b5"></i><i style="background:#e4405f"></i><i style="background:#00aced"></i></div>
  </div>
</article>

<article class="post" style="top:2152px">
  <div class="post-head">
    <span class="post-icon"><svg width="16" height="16" viewBox="0 0 16 16"><path d="M2 14l1-4 8-8 3 3-8 8z" fill="var(--accent)"/></svg></span>
    <h2 class="post-title">I may want a section on finance as well</h2>
  </div>
  <div class="post-meta"><span>Tobin Marsh</span><span>17 Oct 2015</span><span>9835 Views</span><span>Comments</span></div>
  <div class="post-media" role="img" aria-label="Streams of blue binary digits rushing toward a bright light" style="background:radial-gradient(circle at 30% 45%,#dfe9ff,#4a6fd0 25%,#142a7a 60%,#060c2a)"></div>
  <p class="post-excerpt">Money and security have a lot in common: both reward patience, planning and a healthy respect for risk. I am still shaping this section, so expect thoughts on budgets, investing and protecting what you earn.</p>
  <div class="post-actions"><span class="btn">READ MORE</span>
    <div class="share"><i style="background:#3b5998"></i><i style="background:#1da1f2"></i><i style="background:#dd4b39"></i><i style="background:#cb2027"></i><i style="background:#0077b5"></i><i style="background:#e4405f"></i><i style="background:#00aced"></i></div>
  </div>
</article>

<!-- sidebar -->
<div class="widget search">
  <div class="search-box">Search Here...</div>
  <div class="search-btn"><svg width="14" height="14" viewBox="0 0 16 16"><circle cx="6.5" cy="6.5" r="5" fill="none" stroke="#fff" stroke-width="2"/><line x1="10.5" y1="10.5" x2="15" y2="15" stroke="#fff" stroke-width="2"/></svg></div>
</div>

<aside class="widget about">
  <h3 class="widget-title">ABOUT US</h3>
  <div class="about-media" role="img" aria-label="Keyboard with an information security key lit in blue"></div>
  <p>Security architect, author and idea man sharing lessons from work, family and the quiet spaces between.</p>
</aside>

<aside class="widget connect">
  <h3 class="widget-title">STAY CONNECTED</h3>
  <div class="share"><i style="background:#3b5998"></i><i style="background:#1da1f2"></i><i style="background:#dd4b39"></i><i style="background:#cb2027"></i><i style="background:#0077b5"></i><i style="background:#e4405f"></i><i style="background:#00aced"></i></div>
</aside>

<aside class="widget recent">
  <h3 class="widget-title">RECENT POSTS</h3>
  <div class="recent-item"><i class="recent-thumb" role="img" aria-label="Circuit board thumbnail" style="background:linear-gradient(135deg,#1a3a8a,#2a8ad0)"></i><div><h4>SECURE HABITS FOR NEW TEAMS</h4><small>17 Oct 2015</small></div></div>
  <div class="recent-item"><i class="recent-thumb" role="img" aria-label="Glowing network thumbnail" style="background:linear-gradient(135deg,#0a2a6a,#3a7ae0)"></i><div><h4>WRITING FOR YOUNG READERS</h4><small>17 Oct 2015</small></div></div>
  <div class="recent-item"><i class="recent-thumb" role="img" aria-label="Digital lock thumbnail" style="background:linear-gradient(135deg,#102a5a,#4a9ae8)"></i><div><h4>SAFER SPACES ONLINE</h4><small>17 Oct 2015</small></div></div>
  <div class="recent-item"><i class="recent-thumb" role="img" aria-label="Blue data stream thumbnail" style="background:linear-gradient(135deg,#0a1a4a,#2a6ad0)"></i><div><h4>NOTES ON RISK AND MONEY</h4><small>17 Oct 2015</small></div></div>
</aside>

<aside class="widget tweets">
  <h3 class="widget-title">LATEST TWEETS</h3>
  <div class="tweet"><svg width="14" height="14" viewBox="0 0 14 14" style="flex:none;margin-top:2px"><path d="M2 7l3 3 7-7" fill="none" stroke="var(--muted)" stroke-width="2"/></svg><p>New post up on layered defence for small firms, worth a read <a href="#">bramlowt.com/t4x</a><small>2 days ago</small></p></div>
  <div class="tweet"><svg width="14" height="14" viewBox="0 0 14 14" style="flex:none;margin-top:2px"><path d="M2 7l3 3 7-7" fill="none" stroke="var(--muted)" stroke-width="2"/></svg><p>Reading night with the kids tonight, thank you all for the kind notes <a href="#">bramlowt.com/r8k</a><small>4 days ago</small></p></div>
  <div class="tweet"><svg width="14" height="14" viewBox="0 0 14 14" style="flex:none;margin-top:2px"><path d="M2 7l3 3 7-7" fill="none" stroke="var(--muted)" stroke-width="2"/></svg><p>Family safety features just shipped, tell us what you think <a href="#">bramlowt.com/f2m</a><small>1 week ago</small></p></div>
</aside>

<aside class="widget photos">
  <h3 class="widget-title">OUR PHOTOS</h3>
  <div class="photo-grid" role="img" aria-label="Grid of eight technology photo thumbnails">
    <i style="background:#1e4a9a"></i><i style="background:#2a7ad0"></i><i style="background:#3a2a7a"></i><i style="background:#0a3a6a"></i>
    <i style="background:#8a3a1a"></i><i style="background:#1a5a8a"></i><i style="background:#2a9ad0"></i><i style="background:#143060"></i>
  </div>
</aside>

<footer class="site-footer">
  <nav class="footer-nav">
    <a href="#">HOME</a><a href="#">DEMO</a><a href="#">BLOG</a><a href="#">CATEGORIES</a><a href="#">POST FORMATS</a><a href="#">AUTHORS</a><a href="#">PORTFOLIO</a><a href="#">ELEMENTS</a>
  </nav>
  <p class="copyright">COPYRIGHT © 2015 TOBINMARSH &nbsp;|&nbsp; PRIVACY NOTICE</p>
</footer>

</body>
</html>
```